Redesign Comparisson chart - make modern and effective

Use your imaginations to make a powerful distinction between KMV & other holistic modalities. There are 7 elements physical, mental, emotional, energetic, subconscious, superconscious and before and after testing.
We want it to be obvious that KMV is the only modality that works on all these elements simultaneously. We do not want to include any chakras as we want this information to be accepted by a wide range of people and belief systems.'

We want it to look simple but effective. Professional but powerful. We want KMV to stand out even of you eye just passed over i.
Updates

Hi everyone, thanks for your submissions so far. Basically what this image is meant to represent is a comparison chart between all the modalities There are 5 elements physical, mental, emotional, subconscious and superconscious. we want to reflect that KMV is the only modality that works on all these elements simultaneously. As we want the concept to be accepted and not considered woo woo, we want to steer away from chakras.

Target Market(s)

Professionals

Industry/Entity Type

Professional services

Font styles to use
Sans Serif
Other font styles liked:
• Poppins Monserratt

Colors
0094D4
00A9DD
6FCCEA
C7EBF8
E9F6FB

Requirements
Must have
• Clear/professional and clean look. Brand colours and logos. All typography and formats must be cohesive.
Nice to have
• More easy to read, different layout
Should not have
• Do not change the data just the way its presented. No chakras

```html
<!DOCTYPE html>
<html lang="en">
<head>
<meta charset="utf-8">
<title>KMV Comparison Chart</title>
<link rel="stylesheet" href="https://fonts.googleapis.com/css2?family=Montserrat:wght@400;500;600;700&display=swap">
<style>
  :root{
    --brand:#33b7e6;
    --title:#5bc3e8;
    --ink:#1c1c1c;
    --panel:#b0dff2;
    --side:#e9f6fb;
    --label-bg:#117aa7;
    --cell-bg:#e6f4f9;
    --rule:#a9d8ee;
    --band-rule:#117aa7;
    --physical:#e04a3f;
    --mental:#5fbcd9;
    --emotional:#5aaa45;
    --energetic:#f7961f;
    --sub:#f0cf13;
    --super:#8a6aad;
    --before:#d86aa7;
  }
  *{margin:0;padding:0;box-sizing:border-box}
  html,body{width:1200px;height:930px;overflow:hidden;background:#fff}
  body{font-family:'Montserrat',sans-serif;color:var(--ink);position:relative}

  /* header */
  .brand{position:absolute;left:112px;top:22px;width:150px;display:flex;flex-direction:column;align-items:center;gap:8px}
  .brand-dot{width:52px;height:52px;border-radius:50%;background:var(--brand)}
  .brand-name{font-weight:600;font-size:13px;color:var(--brand);white-space:nowrap}
  .headline{position:absolute;left:300px;width:810px;top:30px;text-align:center}
  .headline h1{font-size:22.5px;font-weight:700;color:var(--title);letter-spacing:.2px}
  .headline p{font-size:12.6px;font-weight:500;line-height:16px;margin-top:5px}

  /* panels */
  .chart-panel{position:absolute;left:0;top:123px;width:921px;height:807px;background:var(--panel)}
  .legend-panel{position:absolute;left:921px;top:123px;width:279px;height:807px;background:var(--side)}

  /* chart */
  .grid-bg{position:absolute;left:275px;top:154px;width:574px;height:753px;background:var(--cell-bg);border-radius:10px 10px 0 0}
  .col-heads,.row{position:absolute;left:62px;display:grid;grid-template-columns:213px 77px 77px 77px 77px 83px 83px 90px}
  .col-heads{top:154px;height:45px}
  .col-heads span{display:flex;align-items:center;justify-content:center;text-align:center;font-size:10.5px;font-weight:600;line-height:12px;border-right:1px solid var(--rule);margin:14px 0 2px}
  .col-heads span:first-child,.col-heads span:last-child{border-right:none}
  .c-physical{color:var(--physical)} .c-mental{color:var(--mental)} .c-emotional{color:var(--emotional)}
  .c-energetic{color:var(--energetic)} .c-sub{color:var(--sub)} .c-super{color:var(--super)} .c-before{color:var(--before)}

  .row .label{background:var(--label-bg);color:#fff;font-size:11.6px;font-weight:500;letter-spacing:.45px;line-height:15.6px;padding-left:26px;display:flex;flex-direction:column;justify-content:center;border-bottom:1px solid #5aa7c9;white-space:nowrap}
  .row.first .label{border-radius:14px 0 0 0}
  .row .cell{border-right:1px solid var(--rule);border-bottom:1px solid var(--rule);display:flex;align-items:center;justify-content:center}
  .row .cell:last-child{border-right:none}
  .row.last .label,.row.last .cell{border-bottom:none}

  .gem{width:11px;height:11px;transform:rotate(45deg);display:block}
  .gem.p{background:var(--physical)} .gem.m{background:var(--mental)} .gem.e{background:var(--emotional)}
  .gem.n{background:var(--energetic)} .gem.s{background:var(--sub)} .gem.u{background:var(--super)} .gem.b{background:var(--before)}

  /* highlighted row */
  .hero-row{position:absolute;left:38px;top:497px;width:836px;height:59px;background:#fff;border-radius:8px;box-shadow:0 3px 10px rgba(0,60,100,.18);display:grid;grid-template-columns:237px 77px 77px 77px 77px 83px 83px 90px;align-items:center}
  .hero-name{display:flex;align-items:center;gap:10px;padding-left:56px}
  .hero-dot{width:38px;height:38px;border-radius:50%;background:var(--brand);flex:none}
  .hero-name strong{font-size:12.8px;font-weight:600;letter-spacing:.7px;line-height:17px;color:#1a1a1a}
  .hero-cell{height:40px;display:flex;align-items:center;justify-content:center;border-left:1.5px solid var(--band-rule)}
  .hero-cell .gem{width:19px;height:19px}

  /* legend */
  .legend{position:absolute;left:939px;width:237px}
  .legend h2{font-size:13.5px;font-weight:700;display:flex;align-items:center;gap:6px;margin-left:1px}
  .legend h2::before{content:"";width:7px;height:7px;transform:rotate(45deg);background:currentColor;display:block}
  .legend p{font-size:11.2px;letter-spacing:-.1px;line-height:14.4px;text-align:justify;margin-top:4px}
</style>
</head>
<body>

<header>
  <div class="brand">
    <div class="brand-dot"></div>
    <div class="brand-name">Kind Mind Vitality</div>
  </div>
  <div class="headline">
    <h1>Choose KMV for Fast, Immediate and Powerful Results</h1>
    <p>I must experience healing on all levels, I am not just a body. I want to learn how to heal myself, so I’m not dependent on others.<br>I want to release all my emotional and mental blocks, so I can be the best version of myself.</p>
  </div>
</header>

<section class="chart-panel"></section>
<aside class="legend-panel"></aside>

<div class="grid-bg"></div>

<div class="col-heads">
  <span></span>
  <span class="c-physical">PHYSICAL</span>
  <span class="c-mental">MENTAL</span>
  <span class="c-emotional">EMOTIONAL</span>
  <span class="c-energetic">ENERGETIC</span>
  <span class="c-sub">SUB<br>CONSCIOUS</span>
  <span class="c-super">SUPER<br>CONSCIOUS</span>
  <span class="c-before">BEFORE &amp;<br>AFTER TESTING</span>
</div>

<div class="row first" style="top:199px;height:99px"><div class="label">MASSAGE<br>YOGA<br>NATROPATHY<br>AYURVEDIC MEDICINE<br>WESTERN MEDICINE</div><div class="cell"><i class="gem p"></i></div><div class="cell"></div><div class="cell"></div><div class="cell"></div><div class="cell"></div><div class="cell"></div><div class="cell"></div></div>
<div class="row" style="top:298px;height:30px"><div class="label">PSYCHIC INTUITIVE</div><div class="cell"><i class="gem p"></i></div><div class="cell"><i class="gem m"></i></div><div class="cell"></div><div class="cell"></div><div class="cell"></div><div class="cell"></div><div class="cell"></div></div>
<div class="row" style="top:328px;height:30px"><div class="label">FAMILY CONSTELLATION</div><div class="cell"><i class="gem p"></i></div><div class="cell"><i class="gem m"></i></div><div class="cell"></div><div class="cell"><i class="gem n"></i></div><div class="cell"></div><div class="cell"></div><div class="cell"></div></div>
<div class="row" style="top:358px;height:30px"><div class="label">ACUPUNCTURE</div><div class="cell"><i class="gem p"></i></div><div class="cell"></div><div class="cell"></div><div class="cell"><i class="gem n"></i></div><div class="cell"></div><div class="cell"></div><div class="cell"></div></div>
<div class="row" style="top:388px;height:31px"><div class="label">NUTRITIONAL HEALING</div><div class="cell"><i class="gem p"></i></div><div class="cell"></div><div class="cell"></div><div class="cell"></div><div class="cell"></div><div class="cell"></div><div class="cell"><i class="gem b"></i></div></div>
<div class="row" style="top:419px;height:30px"><div class="label">CHINESE MEDICINE</div><div class="cell"><i class="gem p"></i></div><div class="cell"></div><div class="cell"></div><div class="cell"><i class="gem n"></i></div><div class="cell"></div><div class="cell"></div><div class="cell"><i class="gem b"></i></div></div>
<div class="row" style="top:449px;height:48px"><div class="label">KINESIOLOGY<br>BOWEN THERAPY</div><div class="cell"><i class="gem p"></i></div><div class="cell"></div><div class="cell"></div><div class="cell"></div><div class="cell"><i class="gem s"></i></div><div class="cell"></div><div class="cell"><i class="gem b"></i></div></div>

<div class="row" style="top:556px;height:30px"><div class="label">EFT</div><div class="cell"><i class="gem p"></i></div><div class="cell"><i class="gem m"></i></div><div class="cell"></div><div class="cell"></div><div class="cell"><i class="gem s"></i></div><div class="cell"></div><div class="cell"><i class="gem b"></i></div></div>
<div class="row" style="top:586px;height:31px"><div class="label">CHIROPRACTIC</div><div class="cell"><i class="gem p"></i></div><div class="cell"></div><div class="cell"></div><div class="cell"><i class="gem n"></i></div><div class="cell"><i class="gem s"></i></div><div class="cell"></div><div class="cell"><i class="gem b"></i></div></div>
<div class="row" style="top:617px;height:48px"><div class="label">REIKI<br>CRYSTAL HEALING</div><div class="cell"></div><div class="cell"></div><div class="cell"></div><div class="cell"><i class="gem n"></i></div><div class="cell"></div><div class="cell"></div><div class="cell"></div></div>
<div class="row" style="top:665px;height:30px"><div class="label">ENERGY MEDICINE</div><div class="cell"></div><div class="cell"></div><div class="cell"></div><div class="cell"><i class="gem n"></i></div><div class="cell"></div><div class="cell"></div><div class="cell"><i class="gem b"></i></div></div>
<div class="row" style="top:695px;height:30px"><div class="label">THETA HEALING</div><div class="cell"></div><div class="cell"></div><div class="cell"></div><div class="cell"></div><div class="cell"><i class="gem s"></i></div><div class="cell"><i class="gem u"></i></div><div class="cell"></div></div>
<div class="row" style="top:725px;height:31px"><div class="label">PSYCHOLOGY</div><div class="cell"></div><div class="cell"><i class="gem m"></i></div><div class="cell"></div><div class="cell"></div><div class="cell"></div><div class="cell"></div><div class="cell"></div></div>
<div class="row" style="top:756px;height:47px"><div class="label">MINDFULNESS MEDITATION<br>LIFE COACHING</div><div class="cell"></div><div class="cell"><i class="gem m"></i></div><div class="cell"></div><div class="cell"></div><div class="cell"></div><div class="cell"></div><div class="cell"><i class="gem b"></i></div></div>
<div class="row" style="top:803px;height:49px"><div class="label">HYPNOTHERAPY<br>INNER CHILD HEALING</div><div class="cell"></div><div class="cell"><i class="gem m"></i></div><div class="cell"></div><div class="cell"></div><div class="cell"><i class="gem s"></i></div><div class="cell"></div><div class="cell"></div></div>
<div class="row last" style="top:852px;height:55px"><div class="label">NLP<br>TIMELINE THERAPY</div><div class="cell"></div><div class="cell"><i class="gem m"></i></div><div class="cell"></div><div class="cell"></div><div class="cell"><i class="gem s"></i></div><div class="cell"></div><div class="cell"><i class="gem b"></i></div></div>

<div class="hero-row">
  <div class="hero-name"><span class="hero-dot"></span><strong>KIND MIND<br>VITALITY</strong></div>
  <div class="hero-cell"><i class="gem p"></i></div>
  <div class="hero-cell"><i class="gem m"></i></div>
  <div class="hero-cell"><i class="gem e"></i></div>
  <div class="hero-cell"><i class="gem n"></i></div>
  <div class="hero-cell"><i class="gem s"></i></div>
  <div class="hero-cell"><i class="gem u"></i></div>
  <div class="hero-cell"><i class="gem b"></i></div>
</div>

<section class="legend" style="top:155px">
  <h2 class="c-physical">PHYSICAL</h2>
  <p>Most modalities, including, a western medicine, focus on and treat the physical body only. The KMV process enables you to engage in healing your own body during the session. There is no muscle testing, no hands-on healing and no herbal remedies or medicines.</p>
</section>
<section class="legend" style="top:291px">
  <h2 class="c-mental">MENTAL</h2>
  <p>KMV enables you to use your own consciousness to self-heal. We don’t give you advice or coaching, we allow your mind to heal itself.</p>
</section>
<section class="legend" style="top:383px">
  <h2 class="c-emotional">EMOTIONAL</h2>
  <p>KMV is the only modality that engages your emotions on a physical level. Emotions get stuck in your body and can cause illness over time if left unchecked. KMV enables you you experience fast and powerful emotional releasing.</p>
</section>
<section class="legend" style="top:521px">
  <h2 class="c-energetic">ENERGETIC</h2>
  <p>Most modalities try to move the energy in your body for you. KMV enables and empowers you to do it yourself.</p>
</section>
<section class="legend" style="top:600px">
  <h2 class="c-sub">SUBCONSCIOUS</h2>
  <p>Some modalities, like Kinesiology, access your subconscious through muscle testing. KMV empowers you to access your own subconscious and heal it yourself.</p>
</section>
<section class="legend" style="top:708px">
  <h2 class="c-super">SUPERCONSCIOUS</h2>
  <p>KMV is the only modality the enables you to access and heal your superconscious mind yourself.</p>
</section>
<section class="legend" style="top:789px">
  <h2 class="c-before">BEFORE &amp; AFTER TESTING</h2>
  <p>KMV is the only modality the enables you to provide before and after results, which are documented by us, and analysed by you with our help.</p>
</section>

</body>
</html>
```